Flyer Design Project for Sports Medicine Services

I am a sports medicine doctor specialising in the diagnosis and management of sport and exercise injuries for all ages and levels of activity - from elite to weekend jogger. I work under the Business name Peak Stride Athletics and do have a company logo. I am wanting a flier that I can send to family doctors, physiotherapists and sports clubs explaining who I am what I can offer and why they should send me patients.
- I have a Masters in Sports Medicine (MSportsMed), Diplomas in Obstetrics/Gynaecology (DRANZCOG) and also Paediatrics (DCH) and certificate in advanced clinical hypnosis
-accurate diagnosis and management plan with their regular physio to return the player / athlete to the field / court /gym as soon as safely possible
-hypnosis for sports performance eg anxiety control, confidence and mental rehearsal for individuals and teams
- because there are many possible therapists and therapy options, as a sports doctor I can work out who they need to see a physiotherapist, surgeon, massage therapist chiropractor or podiatrist to return them to activity or whether cortisone, PRP or autologous blood injections are needed
-can provide one point of contact for coaches and clubs for rehabilitation and return to sport advice.
- work with Simon Drewett ex Australian Athlete, a Performance Strategist (NLB listed resource person) and registered Psychologist for best mental preparation for individuals teams and coach development
- can organise rapid access to MRI, ultrasound and specialist appointments if needed
-I work at 3 practices KinetaCare 518 Hollis Rd Hollis 84619027 Monday Wednesday Friday; Brackley Sports Clinic, 193 Brackley Rd, Adelaide 81946372 Tuesday Riverton Hawks Sports Medicine Clinic, Tolvane Arena 8162 5907 Thursday.
-facebook site peakstrideathletics
Updates
Hi All, just to clarify.. My name is Simon Drewett and I am the sports doctor. My wife is Simon Drewett and she is the psychologist. The flier should mainly be advertising my sports medicine services and a byline ( or at least not the first line in the title) about the Performance Strategy and Coach development.
Target Market(s)
family doctors (GPs), Sporting Clubs, Physiotherapists
Industry/Entity Type
Massage
Look and feel

```html
<!DOCTYPE html>
<html lang="en">
<head>
<meta charset="utf-8">
<title>Peak Stride Athletics – Flyer</title>
<link href="https://fonts.googleapis.com/css2?family=Open+Sans:wght@600;700&family=Didact+Gothic&family=Arimo:wght@700&display=swap" rel="stylesheet">
<style>
  :root {
    --sky: #2ea8df;
    --lime: #a9cf38;
    --brand-blue: #2a95d4;
    --white: #ffffff;
    --paper: #ffffff;
  }
  * { box-sizing: border-box; margin: 0; padding: 0; }
  html, body { width: 832px; height: 1200px; overflow: hidden; background: var(--paper); }
  .flyer { position: relative; width: 832px; height: 1200px; overflow: hidden; background: var(--sky); }

  .hero-photo {
    position: absolute; left: 0; top: 0; width: 832px; height: 556px;
    background: linear-gradient(180deg, #bcd8ee 0%, #e7eef3 45%, #f0d7c4 70%, #e9e4df 100%);
  }
  .brand-block {
    position: absolute; left: 0; top: 0; width: 226px; height: 330px;
    background: var(--white);
  }
  .brand {
    position: absolute; left: 8px; top: 36px; width: 212px;
    display: flex; flex-direction: column; align-items: center; gap: 22px;
  }
  .brand-mark { width: 84px; height: 84px; border-radius: 50%; background: var(--lime); }
  .brand-name {
    font-family: "Open Sans", sans-serif; font-weight: 700; font-size: 29px;
    line-height: 1.05; color: var(--brand-blue); text-align: center; letter-spacing: -0.8px;
  }

  .title-box {
    position: absolute; left: 72px; top: 472px; width: 687px; height: 139px;
    background: var(--lime); border-radius: 26px;
    display: flex; align-items: center; justify-content: center;
  }
  .title {
    font-family: "Arimo", Arial, sans-serif; font-weight: 700; font-size: 43px;
    line-height: 55px; color: var(--white); text-align: center;
  }

  .line { display: block; text-align: justify; text-align-last: justify; white-space: nowrap; }
  .line--last { text-align-last: left; }

  .intro {
    position: absolute; left: 98px; top: 628px; width: 642px;
    font-family: "Open Sans", sans-serif; font-weight: 700; font-size: 22px;
    line-height: 30.6px; color: var(--white);
  }

  .services { position: absolute; left: 98px; top: 786px; width: 642px; list-style: none; }
  .services li {
    position: relative; padding-left: 36px; margin-bottom: 23px;
    font-family: "Didact Gothic", sans-serif; font-size: 17.6px; line-height: 24px;
    color: var(--white);
  }
  .services li::before {
    content: ""; position: absolute; left: 0; top: 6px;
    width: 13px; height: 13px; border-radius: 50%; background: var(--white);
  }

  .locations {
    position: absolute; left: 0; top: 1069px; width: 832px; height: 131px;
    background: var(--lime); border-radius: 30px 30px 0 0;
  }
  .location {
    position: absolute; top: 24px;
    font-family: "Didact Gothic", sans-serif; font-size: 14.6px; line-height: 18.6px; color: var(--white);
  }
  .location strong { font-family: "Open Sans", sans-serif; font-weight: 700; font-size: 14.6px; }
  .location--one { left: 31px; }
  .location--two { left: 266px; }
  .location--three { left: 504px; }
</style>
</head>
<body>
<main class="flyer">
  <div class="hero-photo" role="img" aria-label="Photo of a physiotherapist in a light blue shirt assessing an athlete's bent knee"></div>

  <div class="brand-block">
    <div class="brand">
      <span class="brand-mark"></span>
      <span class="brand-name">Peak Stride<br>Athletics</span>
    </div>
  </div>

  <div class="title-box">
    <h1 class="title">Sports Injury Medicine &amp;<br>High Performance Psychology</h1>
  </div>

  <p class="intro">
    <span class="line">Simon Drewett a sports medicine doctor specialising</span>
    <span class="line">in the diagnosis and management of sport and exer-</span>
    <span class="line">cise injuries for all ages and levels of activity - from</span>
    <span class="line line--last">elite to weekend jogger.</span>
  </p>

  <ul class="services">
    <li>
      <span class="line">I have a Masters in Sports Medicine (MSportsMed), Diplomas in</span>
      <span class="line">Obstetrics/Gynaecology (DRANZCOG) and also Paediatrics (DCH)</span>
      <span class="line line--last">and certificate in advanced clinical hypnosis</span>
    </li>
    <li>
      <span class="line">Accurate diagnosis and management plan with their regular physio to</span>
      <span class="line">return the player / athlete to the field / court /gym as soon as safely</span>
      <span class="line line--last">possible</span>
    </li>
    <li>
      <span class="line">Hypnosis for sports performance eg anxiety control, confidence and</span>
      <span class="line line--last">mental rehearsal for individuals and teams</span>
    </li>
  </ul>

  <footer class="locations">
    <div class="location location--one">Monday Wednesday Friday<br><strong>KinetaCare</strong><br>518 Hollis Rd Hollis<br><strong>84619027</strong></div>
    <div class="location location--two">Tuesday<br><strong>Brackley Sports Clinic</strong><br>193 Brackley Rd, Adelaide<br><strong>81946372</strong></div>
    <div class="location location--three">Thursday<br><strong>Riverton Hawks Sports Medicine Clinic</strong><br>Tolvane Arena<br><strong>8162 5907</strong></div>
  </footer>
</main>
</body>
</html>
```